Need a website where people can find information about the newly formed Northmere Valuation Oversight Board. Soon after, we will need a place to publish our findings as we audit each municipality in the State of Northmere. I have a logo (designed by Artwell Hub), a MS Word document showing the content and a set of images to choose from that we can purchase from Pixmarla.com (found here https://www.pixmarla.com/collaboration/boards/-Xq7TbLwRmNoPzYkAuH-Jd)

```html
<!DOCTYPE html>
<html lang="en">
<head>
<meta charset="utf-8">
<title>Northmere Valuation Oversight Board</title>
<link href="https://fonts.googleapis.com/css2?family=Lato:wght@400;700;900&display=swap" rel="stylesheet">
<style>
:root{
  --green:#3a7b16;
  --green-dark:#2f6812;
  --ink:#222226;
  --text:#555a60;
  --soft:#eeeff1;
  --footer:#262628;
  --white:#ffffff;
}
*{box-sizing:border-box;margin:0;padding:0}
html,body{width:1200px;height:3052px;overflow:hidden}
body{font-family:'Lato',sans-serif;color:var(--ink);background:var(--white);position:relative}
.abs{position:absolute}

/* header */
.topbar{top:0;left:0;width:1200px;height:86px;background:var(--white)}
.social{display:flex;gap:18px;align-items:center}
.social span{display:block;width:18px;height:18px;border-radius:50%;background:var(--ink)}
.topbar .social{position:absolute;left:770px;top:34px}
.donate{position:absolute;left:979px;top:20px;width:147px;height:47px;background:var(--ink);color:var(--white);font-weight:700;font-size:19px;letter-spacing:.5px;display:flex;align-items:center;justify-content:center}
.navbar{top:86px;left:0;width:1200px;height:54px;background:var(--green)}
.navbar ul{list-style:none;display:flex;position:absolute;left:213px;top:0;height:54px;align-items:center;gap:30px}
.navbar li{color:var(--white);font-weight:700;font-size:14px;letter-spacing:.2px}
.brand{left:80px;top:14px;width:116px;height:126px;background:var(--white);border:5px solid var(--green);border-radius:10px;display:flex;flex-direction:column;align-items:center;justify-content:center;gap:8px;z-index:2}
.brand .dot{width:40px;height:40px;border-radius:50%;background:var(--green)}
.brand b{color:var(--green);font-weight:900;font-size:22px}

/* hero */
.hero{top:140px;left:0;width:1200px;height:573px;background:linear-gradient(180deg,#1d3f86 0%,#3a5fa0 35%,#9aa3aa 60%,#5f6a4a 85%,#3b4a24 100%)}
.hero h1{position:absolute;top:215px;width:1200px;text-align:center;color:var(--white);font-weight:900;font-size:84px;letter-spacing:1px}
.hero h2{position:absolute;top:310px;width:1200px;text-align:center;color:var(--white);font-weight:900;font-size:30px}
.dots{position:absolute;top:523px;left:563px;display:flex;gap:14px}
.dots i{display:block;width:9px;height:9px;background:var(--white)}
.dots i.on{background:var(--green)}

/* about */
.section-title{position:absolute;width:1200px;text-align:center;font-weight:900;font-size:38px;color:var(--ink)}
.card{top:847px;width:330px;height:361px;border:1px solid #d6d6d6;background:var(--white);text-align:center}
.card .ph{height:193px}
.card h3{font-weight:700;font-size:24px;line-height:31px;margin-top:14px}
.card p{font-size:14px;color:var(--text);line-height:25px;margin-top:10px;padding:0 16px}
.btn{position:absolute;left:98px;top:343px;width:135px;height:39px;background:var(--green);color:var(--white);font-weight:700;font-size:14px;display:flex;align-items:center;justify-content:center}

/* audits */
.audits{top:1298px;left:0;width:1200px;height:390px;background:var(--soft)}
.audits h2{position:absolute;left:75px;top:45px;font-weight:900;font-size:38px}
.audits p{position:absolute;left:75px;top:99px;width:505px;font-size:14.6px;line-height:27.7px;color:var(--text)}
.audits .read{position:absolute;left:75px;top:283px;width:179px;height:50px;background:var(--green);border-radius:5px;color:var(--white);font-weight:700;font-size:15px;display:flex;align-items:center;justify-content:center}
.audits .ph{position:absolute;left:577px;top:0;width:623px;height:390px;background:linear-gradient(135deg,#2c2f33 0%,#5b6068 40%,#c9cbcc 70%,#e4e2dc 100%);clip-path:polygon(51px 0,623px 0,623px 390px,0 390px)}

/* recommendations */
.rec{top:1828px;width:271px;text-align:center}
.rec .icon{width:106px;height:106px;border-radius:50%;background:var(--green);border:4px solid #dfe6db;margin:0 auto;display:flex;align-items:center;justify-content:center}
.rec h3{font-weight:700;font-size:25px;margin-top:26px}
.rec p{font-size:15px;line-height:23.5px;color:var(--text);margin:12px auto 0;width:240px}
.arrow{top:1932px}

/* volunteers */
.volunteers{top:2135px;left:0;width:1200px;height:518px;background:var(--soft)}
.vol{top:2295px;width:362px;height:219px}
.vol .ph{position:absolute;left:0;top:0;width:206px;height:219px}
.vol .info{position:absolute;left:124px;top:116px;width:238px;height:103px;background:var(--soft);padding:4px 0 0 14px}
.vol h4{color:var(--green);font-weight:900;font-size:19px;white-space:nowrap}
.vol p{font-size:14.5px;line-height:23px;color:var(--text);margin-top:4px;width:190px}

/* footer */
.footer{top:2653px;left:0;width:1200px;height:399px;background:var(--footer)}
.newsletter{top:2600px;left:75px;width:1050px;height:104px;background:var(--green);z-index:2}
.newsletter h3{position:absolute;left:70px;top:35px;color:var(--white);font-weight:700;font-size:28px;letter-spacing:.5px}
.newsletter .field{position:absolute;left:391px;top:28px;width:389px;height:48px;background:var(--white);font-size:14px;font-weight:700;color:#444;padding:16px 14px}
.newsletter .sub{position:absolute;left:790px;top:28px;width:169px;height:48px;background:#1a1a1c;color:var(--white);font-weight:700;font-size:18px;display:flex;align-items:center;justify-content:center}
.foot-brand{left:80px;top:2768px;width:116px;height:122px;background:var(--white);border-radius:10px;display:flex;flex-direction:column;align-items:center;justify-content:center;gap:8px}
.foot-brand .dot{width:40px;height:40px;border-radius:50%;background:var(--green)}
.foot-brand b{color:var(--green);font-weight:900;font-size:22px}
.copy{left:75px;top:2905px;color:var(--white);font-size:13px;line-height:20px}
.col{top:2752px;color:var(--white)}
.col h5{font-weight:700;font-size:19px;margin-bottom:10px}
.col li{list-style:none;font-size:14px;line-height:31.5px;color:#d8d8d8}
.contact li{display:flex;gap:16px;align-items:center;white-space:nowrap}
.footer-social{left:913px;top:2948px}
.footer-social span{background:var(--white);width:20px;height:20px}
</style>
</head>
<body>

<header class="abs topbar">
  <div class="social" aria-label="Social links"><span></span><span></span><span></span><span></span><span></span></div>
  <div class="donate">DONATE</div>
</header>
<nav class="abs navbar">
  <ul>
    <li>WHO WE ARE</li><li>BLOG</li><li>AUDITS</li><li>NVOB RECOMMENDATIONS</li><li>MEET THE VOLUNTEERS</li><li>CORRECTIONS</li><li>CONTACT US</li>
  </ul>
</nav>
<div class="abs brand"><span class="dot"></span><b>NVOB</b></div>

<section class="abs hero" role="img" aria-label="State capitol building under a blue sky">
  <h1>WELCOME TO NVOB</h1>
  <h2>NORTHMERE VALUATION OVERSIGHT BOARD</h2>
  <div class="dots"><i class="on"></i><i></i><i></i><i></i></div>
</section>

<h2 class="section-title" style="top:768px">ABOUT US</h2>
<article class="abs card" style="left:75px">
  <div class="ph" role="img" aria-label="Metal gears engraved with audit words" style="background:linear-gradient(135deg,#3a3a3a,#9a9a9a 50%,#4a4a4a)"></div>
  <h3>Who<br>We Are</h3>
  <p>Sed in nunc lorem luctus hendrerit facilisis. Phasellus sit amet enim quis..</p>
  <div class="btn">MORE DETAILS</div>
</article>
<article class="abs card" style="left:435px">
  <div class="ph" role="img" aria-label="Property tax note beside a tree and house plan" style="background:linear-gradient(135deg,#6aa3b8,#c9a470 50%,#d8b47a)"></div>
  <h3>Northmere’s Non-Uniform<br>Property Tax Problem</h3>
  <p>Sed in nunc lorem luctus hendrerit facilisis. Phasellus sit amet enim quis..</p>
  <div class="btn">MORE DETAILS</div>
</article>
<article class="abs card" style="left:796px">
  <div class="ph" role="img" aria-label="Hands writing notes beside a laptop and charts" style="background:linear-gradient(135deg,#dfe6f0,#b8c4d6 50%,#2a2d33)"></div>
  <h3>What is Uniform<br>Taxation?</h3>
  <p>Sed in nunc lorem luctus hendrerit facilisis. Phasellus sit amet enim quis..</p>
  <div class="btn">MORE DETAILS</div>
</article>

<section class="abs audits">
  <h2>AUDITS</h2>
  <p>Sed in nunc lorem. Sed luctus hendrerit facilisis sit amet enim quis nibh ultricies convallis. Aliquam egestas dapibus odio ut lobortis mattis nisi, in convallis enim. Proin a diam et diam efficitur ultricies nec eget tellus. Proin ultricies purus sed dui efficitur rutrum. Nulla viverra purus a sapien varius, a posuere lectus tristique. Sed hendrerit eleifend odio,<br>non pulvinar sapien ullamcorper sed.</p>
  <div class="read">READ MORE</div>
  <div class="ph" role="img" aria-label="Hand with pen over a spreadsheet beside a keyboard"></div>
</section>

<h2 class="section-title" style="top:1741px">NVOB RECOMMENDATIONS</h2>
<svg class="abs arrow" style="left:46px" width="16" height="28" viewBox="0 0 16 28"><path d="M14 2 2 14l12 12" fill="none" stroke="#222226" stroke-width="2.5"/></svg>
<svg class="abs arrow" style="left:1138px" width="16" height="28" viewBox="0 0 16 28"><path d="M2 2l12 12L2 26" fill="none" stroke="#222226" stroke-width="2.5"/></svg>

<div class="abs rec" style="left:58px">
  <div class="icon"><svg width="56" height="50" viewBox="0 0 56 50" fill="none" stroke="#fff" stroke-width="2.5"><path d="M4 16h48L28 4z"/><path d="M8 16v26M18 16v26M28 16v26M38 16v26M48 16v26"/><path d="M2 46h52"/></svg></div>
  <h3>For Municipalities</h3>
  <p>Sed in nunc lorem luctus hendrerit facilisis. Phasellus sit amet enim quis..</p>
</div>
<div class="abs rec" style="left:329px">
  <div class="icon"><svg width="52" height="52" viewBox="0 0 52 52" fill="none" stroke="#fff" stroke-width="2.5"><rect x="6" y="4" width="30" height="40"/><path d="M12 14h18M12 22h12M12 30h10"/><circle cx="36" cy="34" r="8"/><path d="M42 40l7 7"/></svg></div>
  <h3>For Boards of Review</h3>
  <p>Sed in nunc lorem luctus hendrerit facilisis. Phasellus sit amet enim quis..</p>
</div>
<div class="abs rec" style="left:601px">
  <div class="icon"><svg width="46" height="56" viewBox="0 0 46 56" fill="none" stroke="#fff" stroke-width="2.5"><path d="M6 4h26l8 8v32H6z"/><path d="M12 16h22M12 24h22M12 32h16"/><path d="M23 44v10"/></svg></div>
  <h3>For Legislators</h3>
  <p>Sed in nunc lorem luctus hendrerit facilisis. Phasellus sit amet enim quis..</p>
</div>
<div class="abs rec" style="left:871px">
  <div class="icon"><svg width="50" height="52" viewBox="0 0 50 52" fill="none" stroke="#fff" stroke-width="2.5"><path d="M6 4h26l8 8v36H6z"/><path d="M12 28h18M12 35h18M12 42h14"/><ellipse cx="40" cy="34" rx="6" ry="3"/><path d="M34 34v10c0 2 12 2 12 0V34"/><text x="11" y="20" fill="#fff" stroke="none" font-family="Lato,sans-serif" font-weight="700" font-size="11">TAX</text></svg></div>
  <h3>For Taxpayers</h3>
  <p>Sed in nunc lorem luctus hendrerit facilisis. Phasellus sit amet enim quis..</p>
</div>

<section class="abs volunteers"></section>
<h2 class="section-title" style="top:2195px">MEET THE VOLUNTEERS</h2>
<div class="abs vol" style="left:75px">
  <div class="ph" role="img" aria-label="Volunteer portrait outdoors with a horse on grass" style="background:linear-gradient(135deg,#5a3a22,#6f7f3a 50%,#4a6a2a)"></div>
  <div class="info"><h4>LORNA BELVEDERE</h4><p>Sed in nunc lorem luctus hendrerit facilisissellus sit ametenim quis..</p></div>
</div>
<div class="abs vol" style="left:434px">
  <div class="ph" role="img" aria-label="Volunteer portrait in a suit before greenery" style="background:linear-gradient(135deg,#3f6a2a,#6a7a5a 50%,#22262c)"></div>
  <div class="info"><h4>TOMAS WRENFIELD</h4><p>Sed in nunc lorem luctus hendrerit facilisissellus sit ametenim quis..</p></div>
</div>
<div class="abs vol" style="left:794px">
  <div class="ph" role="img" aria-label="Black and white volunteer portrait in a suit" style="background:linear-gradient(135deg,#e6e6e6,#8a8a8a 50%,#2a2a2a)"></div>
  <div class="info"><h4>EDGAR HOLLINSBY</h4><p>Sed in nunc lorem luctus hendrerit facilisissellus sit ametenim quis..</p></div>
</div>

<footer class="abs footer"></footer>
<div class="abs newsletter">
  <h3>NEWSLETTER SIGN UP</h3>
  <div class="field">Enter Email Address</div>
  <div class="sub">Subscribe Now</div>
</div>
<div class="abs foot-brand"><span class="dot"></span><b>NVOB</b></div>
<div class="abs copy">Copyright © 2022 Company Name<br>All Rights Reserved</div>

<div class="abs col" style="left:347px">
  <h5>Site Map</h5>
  <ul><li>Who We Are</li><li>Blog</li><li>Audits</li><li>NVOB Recommendations</li><li>Meet the Volunteers</li><li>Corrections</li><li>Contact us</li></ul>
</div>
<div class="abs col" style="left:612px;top:2750px">
  <h5>NVOB Recommendations</h5>
  <ul><li>For Municipalities</li><li>For Boards of Review</li><li>For the Department of Revenue</li><li>For Legislators</li><li>For Taxpayers</li></ul>
</div>
<div class="abs col contact" style="left:913px;top:2750px">
  <h5>Contact Info</h5>
  <ul style="width:250px">
    <li style="display:block;white-space:normal;width:170px;line-height:23px;margin-bottom:8px">5518 - 47 Ridgeway Lane Nullam sit amet sapien sollicitudin</li>
    <li><svg width="14" height="14" viewBox="0 0 14 14"><path d="M3 1l2 3-1.5 1.5a8 8 0 0 0 5 5L10 9l3 2-1 2.5C6 13.5.5 8 .5 2z" fill="#fff"/></svg>1-800-555-0142</li>
    <li><svg width="14" height="11" viewBox="0 0 14 11"><rect width="14" height="11" fill="#fff"/><path d="M0 0l7 6 7-6" fill="none" stroke="#262628" stroke-width="1.3"/></svg>hello@northmere-board.org</li>
  </ul>
</div>
<div class="abs social footer-social" aria-label="Social links"><span></span><span></span><span></span><span></span><span></span></div>

</body>
</html>
```